Visit card

Industry/Entity Type

Health Care

Contact Information for Business Card

O VITALIS SYSTEMS
Odile Brevard - chef de Projet

Requirements
Must have
• 318 Gaston Lemaire Street 59710 VARENVILLE Tel: 33 (0) 327 481 605 Mobile: 06 42 19 37 64 Web: www.quorvexsystems.example Contact: o.brevard@o-vitalissystems.example
Should not have
• Respect for color

```html
<!DOCTYPE html>
<html lang="fr">
<head>
<meta charset="utf-8">
<title>O Vitalis Systems – Carte de visite</title>
<link rel="stylesheet" href="https://fonts.googleapis.com/css2?family=Montserrat:wght@500;600;700&family=Lato:wght@400&display=swap">
<style>
  :root {
    --backdrop: #5b5b5d;
    --card-dark: #4a4a4c;
    --card-light: #ffffff;
    --brand-red: #e5202e;
    --ink: #333335;
    --ink-soft: #4a4a4a;
    --rule: #555555;
    --white: #ffffff;
  }
  * { margin: 0; padding: 0; box-sizing: border-box; }
  html, body {
    width: 1200px; height: 895px; overflow: hidden;
    background: var(--backdrop);
  }
  .canvas {
    position: relative; width: 1200px; height: 895px;
    display: flex; flex-direction: column; align-items: center; justify-content: center; gap: 44px;
  }
  .card {
    width: 580px; height: 330px; border-radius: 26px;
    position: relative;
  }
  .card--front {
    background: var(--card-dark);
    display: flex; align-items: center; justify-content: center; gap: 22px;
  }
  .brand-dot {
    width: 78px; height: 78px; border-radius: 50%;
    background: var(--white);
  }
  .brand-name {
    font-family: "Montserrat", sans-serif; font-weight: 700;
    font-size: 34px; letter-spacing: 2px; color: var(--white);
  }
  .card--back {
    background: var(--card-light);
    display: flex; align-items: center;
  }
  .identity {
    width: 250px; text-align: right; padding-right: 26px; margin-top: 40px;
  }
  .identity__name {
    font-family: "Montserrat", sans-serif; font-weight: 600;
    font-size: 23px; color: var(--brand-red); text-transform: uppercase; letter-spacing: -0.3px;
  }
  .identity__role {
    font-family: "Lato", sans-serif; font-size: 17px; color: var(--ink-soft); margin-top: 1px;
  }
  .divider {
    width: 1.5px; height: 150px; background: var(--rule);
  }
  .contact {
    padding-left: 22px;
    font-family: "Lato", sans-serif; font-size: 15px; color: var(--ink); line-height: 20px;
    list-style: none;
  }
  .contact__item { display: flex; align-items: center; gap: 7px; white-space: nowrap; }
  .contact__icon { width: 14px; height: 14px; flex: none; }
</style>
</head>
<body>
<main class="canvas">
  <section class="card card--front" aria-label="Recto">
    <span class="brand-dot" aria-hidden="true"></span>
    <span class="brand-name">O VITALIS SYSTEMS</span>
  </section>

  <section class="card card--back" aria-label="Verso">
    <div class="identity">
      <p class="identity__name">Odile Brevard</p>
      <p class="identity__role">Chef de Projet</p>
    </div>
    <span class="divider" aria-hidden="true"></span>
    <ul class="contact">
      <li class="contact__item">318 Rue Gaston Lemaire</li>
      <li class="contact__item">59710 VARENVILLE</li>
      <li class="contact__item">
        <svg class="contact__icon" viewBox="0 0 14 14" aria-hidden="true"><circle cx="7" cy="7" r="7" fill="var(--brand-red)"/><rect x="4.6" y="3" width="4.8" height="8" rx="1" fill="none" stroke="#fff" stroke-width="1.2"/></svg>
        06 42 19 37 64
      </li>
      <li class="contact__item">
        <svg class="contact__icon" viewBox="0 0 14 14" aria-hidden="true"><circle cx="7" cy="7" r="7" fill="var(--brand-red)"/><path d="M4.3 4.2c.5-.5 1-.4 1.3 0l.6 1c.2.4 0 .7-.3 1-.2.2 1 1.6 1.8 1.9.3-.3.6-.5 1-.3l1 .6c.4.3.5.8 0 1.3-1.3 1.3-5.8-3-5.4-5.5z" fill="#fff"/></svg>
        +33 (0) 327 481 605
      </li>
      <li class="contact__item">
        <svg class="contact__icon" viewBox="0 0 14 14" aria-hidden="true"><circle cx="7" cy="7" r="7" fill="var(--brand-red)"/><rect x="3.5" y="4.5" width="7" height="5" fill="none" stroke="#fff" stroke-width="1"/><path d="M3.5 4.5 7 7.3l3.5-2.8" fill="none" stroke="#fff" stroke-width="1"/></svg>
        o.brevard@o-vitalissystems.example
      </li>
      <li class="contact__item">
        <svg class="contact__icon" viewBox="0 0 14 14" aria-hidden="true"><circle cx="7" cy="7" r="7" fill="var(--brand-red)"/><circle cx="7" cy="7" r="3.8" fill="none" stroke="#fff" stroke-width="0.9"/><ellipse cx="7" cy="7" rx="1.6" ry="3.8" fill="none" stroke="#fff" stroke-width="0.9"/><path d="M3.2 7h7.6" stroke="#fff" stroke-width="0.9"/></svg>
        www.quorvexsystems.example
      </li>
    </ul>
  </section>
</main>
</body>
</html>
```